BRISKEL Need a luxury modern business card designed.

Need a luxury modern business card designed. refer to the uploaded files for the company name and logo in the zip file under source files. i will making my descion on monday. so please send in before then so if we need to edit we will have the time. we have a trade show coming up and im on a deadline for printer.

Target Market(s)

high end clients

Contact Information for Business Card

Company nAme and logo. Tobias Fennick Co-Founder / Project Manager Office # 555-318-7094 Cell # 555-642-1586 BRISKEL.CA Tobias@briskel-example.ca

Font styles to use
Other font styles liked:
• Modern

Requirements
Must have
• Company name and logo, contact info, using the black, gold and white color scheme.

```html
<!DOCTYPE html>
<html lang="en">
<head>
<meta charset="utf-8">
<title>BRISKEL Business Card</title>
<link rel="stylesheet" href="https://fonts.googleapis.com/css2?family=Montserrat:wght@300;400;500&display=swap">
<style>
  :root {
    --bg: #1a1a1a;
    --card: #333333;
    --edge: #a89666;
    --gold: #ad9b66;
    --white: #f4f4f2;
    --muted: #d9d9d6;
  }
  * { box-sizing: border-box; margin: 0; padding: 0; }
  html, body { width: 1200px; height: 900px; overflow: hidden; }
  body {
    background: var(--bg);
    font-family: "Montserrat", sans-serif;
    display: flex;
    flex-direction: column;
    align-items: center;
    justify-content: center;
    gap: 30px;
  }
  .card {
    position: relative;
    width: 700px;
    height: 400px;
    background: var(--card);
    border: 3px solid var(--edge);
  }
  .wordmark {
    font-weight: 300;
    color: var(--white);
    letter-spacing: 0.22em;
  }
  .card-front .wordmark {
    position: absolute;
    right: 60px;
    top: 80px;
    font-size: 50px;
  }
  .card-back .brand {
    position: absolute;
    top: 70px;
    left: 0;
    right: 0;
    display: flex;
    justify-content: center;
    align-items: center;
    gap: 16px;
  }
  .card-back .brand-mark {
    width: 12px;
    height: 12px;
    background: var(--gold);
  }
  .card-back .wordmark { font-size: 40px; }
  .rule {
    position: absolute;
    left: 60px;
    right: 60px;
    top: 185px;
    height: 1px;
    background: var(--gold);
  }
  .person {
    position: absolute;
    left: 40px;
    width: 300px;
    top: 255px;
    text-align: right;
  }
  .person-name {
    color: var(--gold);
    font-weight: 500;
    font-size: 24px;
    letter-spacing: 0.02em;
    text-transform: uppercase;
  }
  .person-role {
    color: var(--white);
    font-size: 17px;
    margin-top: 4px;
  }
  .divider {
    position: absolute;
    left: 360px;
    top: 240px;
    width: 1px;
    height: 110px;
    background: var(--gold);
  }
  .contacts {
    position: absolute;
    left: 380px;
    top: 238px;
    list-style: none;
    color: var(--white);
    font-size: 18px;
    line-height: 28px;
  }
  .contacts li { display: flex; align-items: center; gap: 12px; }
  .contacts svg { width: 18px; height: 18px; flex: none; }
  .contacts .accent { color: var(--gold); font-weight: 500; }
</style>
</head>
<body>
  <section class="card card-front">
    <div class="wordmark">BRISKEL</div>
  </section>

  <section class="card card-back">
    <div class="brand">
      <span class="brand-mark"></span>
      <span class="wordmark">BRISKEL</span>
    </div>
    <div class="rule"></div>

    <div class="person">
      <div class="person-name">Tobias Fennick</div>
      <div class="person-role">Co-Founder | Project Manager</div>
    </div>

    <div class="divider"></div>

    <ul class="contacts">
      <li>
        <svg viewBox="0 0 24 24" fill="none" stroke="#d9d9d6" stroke-width="1.6"><circle cx="12" cy="12" r="10"/><path d="M8.5 7.5l2 2-1 1.5c.8 1.6 2 2.8 3.5 3.5l1.5-1 2 2-1.2 1.3c-3.5-.4-7-3.9-7.4-7.4z"/></svg>
        <span>555-318-7094</span>
      </li>
      <li>
        <svg viewBox="0 0 24 24" fill="none" stroke="#d9d9d6" stroke-width="1.6"><rect x="7" y="2.5" width="10" height="19" rx="2"/><path d="M11 18h2"/></svg>
        <span>555-642-1586</span>
      </li>
      <li>
        <svg viewBox="0 0 24 24" fill="none" stroke="#d9d9d6" stroke-width="1.6"><rect x="2.5" y="5.5" width="19" height="13"/><path d="M2.5 5.5l9.5 7 9.5-7"/></svg>
        <span>Tobias@briskel-example.ca</span>
      </li>
      <li>
        <svg viewBox="0 0 24 24" fill="none" stroke="#d9d9d6" stroke-width="1.6"><circle cx="12" cy="12" r="9.5"/><ellipse cx="12" cy="12" rx="4" ry="9.5"/><path d="M2.5 12h19M4 7h16M4 17h16"/></svg>
        <span>www.<span class="accent">briskel</span>.ca</span>
      </li>
    </ul>
  </section>
</body>
</html>
```